Garlic Farm for Farm Sales/Restaurant sales

Need a professional, but appealing to agriculture world. We are selling 27 kinds of Organic Garlic from a farm in Simla,CO. I have uploaded logo and business information-we are going to need a template, because I will need to use it for four separate people.
-We are trying to appeal to Farm to table restaurants
-As well as growers/farmers

Target Market(s)

Agriculture Sales/Restaurants-Organic

Industry/Entity Type

Agriculture

Contact Information for Business Card

Want it to look more unique then your average kelto stock card- I want it to look amazing

Font styles to use
Sans Serif

Colors
0455a3
ec1f27
fbed22
ffffff

Requirements
Must have
• Just be creative
Nice to have
• Colorful
Should not have
• plain

```html
<!DOCTYPE html>
<html lang="en">
<head>
<meta charset="utf-8">
<title>Ridgeline Gourmet Garlic – Business Card</title>
<link href="https://fonts.googleapis.com/css2?family=Josefin+Sans:wght@400;600;700&display=swap" rel="stylesheet">
<style>
  :root {
    --navy: #1c2f5f;
    --red: #c8202b;
    --yellow: #fbdd1a;
    --white: #ffffff;
    --backdrop: #e9e9ec;
    --font: "Josefin Sans", sans-serif;
  }
  * { box-sizing: border-box; margin: 0; padding: 0; }
  html, body { width: 1200px; height: 900px; overflow: hidden; }
  body { background: var(--backdrop); font-family: var(--font); position: relative; }

  .card {
    position: absolute;
    width: 700px;
    height: 400px;
    left: 250px;
    border-radius: 26px;
    overflow: hidden;
    box-shadow: 0 8px 24px rgba(0,0,0,0.18);
  }
  .card svg.card-art { position: absolute; inset: 0; }

  /* Front */
  .card--front { top: 30px; background: var(--navy); }
  .brand {
    position: absolute;
    right: 60px;
    top: 120px;
    display: flex;
    align-items: center;
    gap: 18px;
  }
  .brand__dot { width: 62px; height: 62px; border-radius: 50%; background: var(--red); flex: none; }
  .brand__name {
    color: var(--white);
    font-weight: 700;
    font-size: 40px;
    line-height: 1.05;
    text-transform: lowercase;
  }

  /* Back */
  .card--back { top: 470px; background: var(--white); }
  .back-brand {
    position: absolute;
    left: 150px;
    top: 80px;
    display: flex;
    align-items: center;
    gap: 16px;
  }
  .back-brand__dot { width: 54px; height: 54px; border-radius: 50%; background: var(--red); flex: none; }
  .back-brand__name {
    color: var(--navy);
    font-weight: 700;
    font-size: 32px;
    line-height: 1.05;
    text-transform: lowercase;
  }
  .person {
    position: absolute;
    left: 40px;
    bottom: 32px;
    color: var(--white);
  }
  .person__name {
    font-size: 30px;
    font-weight: 600;
    letter-spacing: 1px;
    text-transform: uppercase;
  }
  .person__name .surname { color: var(--red); }
  .person__address { font-size: 18px; margin-top: 10px; }

  .contacts {
    position: absolute;
    right: 28px;
    top: 196px;
    list-style: none;
    color: var(--white);
    font-size: 17px;
  }
  .contacts li {
    display: flex;
    align-items: center;
    justify-content: flex-end;
    gap: 10px;
    height: 30px;
  }
  .contacts .accent { color: var(--red); }
  .contact-icon {
    width: 18px; height: 18px;
    background: var(--red);
    border-radius: 3px;
    display: flex; align-items: center; justify-content: center;
    flex: none;
  }
</style>
</head>
<body>

  <section class="card card--front" aria-label="Card front">
    <svg class="card-art" width="700" height="400" viewBox="0 0 700 400" aria-hidden="true">
      <rect class="band-red" x="0" y="298" width="700" height="50" fill="#c8202b"/>
      <g class="social-dots" fill="#ffffff">
        <circle cx="430" cy="323" r="14"/>
        <circle cx="505" cy="323" r="14"/>
        <circle cx="580" cy="323" r="14"/>
        <circle cx="655" cy="323" r="14"/>
      </g>
    </svg>
    <div class="brand">
      <span class="brand__dot"></span>
      <span class="brand__name">ridgeline<br>gourmet garlic</span>
    </div>
  </section>

  <section class="card card--back" aria-label="Card back">
    <svg class="card-art" width="700" height="400" viewBox="0 0 700 400" aria-hidden="true">
      <path class="swoosh-navy" d="M0 300 C 240 290, 470 230, 700 150 L 700 400 L 0 400 Z" fill="#1c2f5f"/>
      <path class="swoosh-yellow" d="M0 282 C 240 272, 470 212, 700 128" fill="none" stroke="#fbdd1a" stroke-width="7"/>
    </svg>

    <div class="back-brand">
      <span class="back-brand__dot"></span>
      <span class="back-brand__name">ridgeline<br>gourmet garlic</span>
    </div>

    <div class="person">
      <p class="person__name">Dana <span class="surname">Fulton</span></p>
      <p class="person__address">P.O. Box 12 Larkton, CO 80812</p>
    </div>

    <ul class="contacts">
      <li>719-555-0147
        <span class="contact-icon">
          <svg width="12" height="12" viewBox="0 0 24 24" aria-hidden="true"><path d="M6.6 10.8a15 15 0 0 0 6.6 6.6l2.2-2.2c.3-.3.7-.4 1-.2 1.1.4 2.3.6 3.6.6.6 0 1 .4 1 1V20c0 .6-.4 1-1 1C10.6 21 3 13.4 3 4c0-.6.4-1 1-1h3.5c.6 0 1 .4 1 1 0 1.3.2 2.5.6 3.6.1.3 0 .7-.2 1z" fill="#fff"/></svg>
        </span>
      </li>
      <li>Dana@RGGarlic.com
        <span class="contact-icon">
          <svg width="12" height="12" viewBox="0 0 24 24" aria-hidden="true"><rect x="3" y="6" width="18" height="12" rx="1" fill="none" stroke="#fff" stroke-width="2"/><path d="M3 7l9 6 9-6" fill="none" stroke="#fff" stroke-width="2"/></svg>
        </span>
      </li>
      <li><span>www.<span class="accent">RG</span>Garlic.com</span>
        <span class="contact-icon">
          <svg width="12" height="12" viewBox="0 0 24 24" aria-hidden="true"><circle cx="12" cy="12" r="9" fill="none" stroke="#fff" stroke-width="2"/><path d="M3 12h18M12 3c3 3 3 15 0 18M12 3c-3 3-3 15 0 18" fill="none" stroke="#fff" stroke-width="1.6"/></svg>
        </span>
      </li>
    </ul>
  </section>

</body>
</html>
```